Unique Business Card Design

Unique Business Card design for our orthotic and prosthetic company. Our logo is on our website, color is light blue. Unique shape (artificial leg shaped, vertical, etc..) preferred. Logo, business name, individual name and basic demographics needed.

Industry/Entity Type

Business

Contact Information for Business Card

Logo, Industry, Phone # Logo, "Prosthetic & Orthotic Services" Place to add individual name and contact info

Colors
cee9f5

Requirements
Must have
• The icon must be there, placement of "Prosthetic & Orthotic Services" can be moved
Nice to have
• Like the mix of light blue, and a little darker blue. One design included the icons from my website which was a nice touch

```html
<!DOCTYPE html>
<html lang="en">
<head>
<meta charset="utf-8">
<title>Limbwell Inc — Business Card</title>
<link rel="stylesheet" href="https://fonts.googleapis.com/css2?family=Open+Sans:wght@400;600;700&family=Parisienne&display=swap">
<style>
  :root {
    --brand-blue: #1a74d0;
    --brand-blue-deep: #1565bf;
    --paper: #ffffff;
    --stage: #eef1f4;
    --ink-light: #ffffff;
  }
  * { box-sizing: border-box; margin: 0; padding: 0; }
  html, body { width: 1200px; height: 900px; overflow: hidden; }
  body {
    background: var(--stage);
    font-family: "Open Sans", Arial, sans-serif;
    position: relative;
  }
  .card {
    position: absolute;
    width: 560px;
    height: 320px;
    overflow: hidden;
    box-shadow: 0 6px 18px rgba(0,0,0,0.12);
  }
  .card--front { left: 90px; top: 100px; background: var(--brand-blue); }
  .card--back { left: 550px; top: 480px; background: var(--paper); }

  .brand { position: absolute; display: flex; align-items: center; gap: 22px; }
  .brand-mark { width: 96px; height: 96px; border-radius: 50%; flex: none; }
  .brand-text { display: flex; flex-direction: column; }
  .brand-name {
    font-weight: 600;
    font-size: 30px;
    letter-spacing: 0.5px;
    line-height: 1.1;
    padding-bottom: 6px;
    border-bottom: 2px solid currentColor;
  }
  .brand-tagline {
    font-family: "Parisienne", cursive;
    font-size: 19px;
    padding-top: 4px;
    padding-left: 24px;
  }

  .card--front .brand { left: 110px; top: 105px; }
  .card--front .brand-mark { background: var(--paper); }
  .card--front .brand-text { color: var(--ink-light); }

  .card--back .brand { left: 110px; top: 50px; }
  .card--back .brand-mark { background: var(--brand-blue); }
  .card--back .brand-text { color: var(--brand-blue); }

  .contact-band {
    position: absolute;
    left: 0; right: 0; bottom: 0;
    height: 138px;
    background: var(--brand-blue-deep);
    color: var(--ink-light);
  }
  .person {
    position: absolute;
    right: 284px; top: 22px;
    text-align: right;
  }
  .person-name { font-weight: 700; font-size: 20px; line-height: 1.2; }
  .person-title { font-size: 15px; }
  .divider {
    position: absolute;
    left: 286px; top: 18px;
    width: 1px; height: 52px;
    background: var(--ink-light);
  }
  .contact-list {
    position: absolute;
    left: 298px; top: 14px;
    list-style: none;
    font-size: 13.5px;
    line-height: 20px;
  }
  .contact-list li { display: flex; align-items: center; gap: 6px; }
  .contact-list .phone { font-weight: 700; font-size: 15px; }
  .contact-list svg { width: 11px; height: 11px; fill: var(--ink-light); flex: none; }
  .address {
    position: absolute;
    left: 150px; bottom: 22px;
    font-size: 16px;
  }
</style>
</head>
<body>

  <section class="card card--front" aria-label="Business card front">
    <div class="brand">
      <span class="brand-mark"></span>
      <div class="brand-text">
        <span class="brand-name">LIMBWELL INC</span>
        <span class="brand-tagline">Prosthetic &amp; Orthotic Services</span>
      </div>
    </div>
  </section>

  <section class="card card--back" aria-label="Business card back">
    <div class="brand">
      <span class="brand-mark"></span>
      <div class="brand-text">
        <span class="brand-name">LIMBWELL INC</span>
        <span class="brand-tagline">Prosthetic &amp; Orthotic Services</span>
      </div>
    </div>

    <div class="contact-band">
      <div class="person">
        <div class="person-name">Daniel Reyes</div>
        <div class="person-title">Managing Director</div>
      </div>
      <span class="divider"></span>
      <ul class="contact-list">
        <li class="phone">
          <svg viewBox="0 0 24 24" aria-hidden="true"><path d="M6.6 10.8a15.1 15.1 0 0 0 6.6 6.6l2.2-2.2a1 1 0 0 1 1-.25 11.4 11.4 0 0 0 3.6.57 1 1 0 0 1 1 1V20a1 1 0 0 1-1 1A17 17 0 0 1 3 4a1 1 0 0 1 1-1h3.5a1 1 0 0 1 1 1c0 1.25.2 2.45.57 3.6a1 1 0 0 1-.25 1z"/></svg>
          (555) 014-2260
        </li>
        <li>
          <svg viewBox="0 0 24 24" aria-hidden="true"><path d="M2 5h20v14H2z M2 5l10 8 10-8" stroke="#1565bf" stroke-width="1.5"/></svg>
          info@limbwellinc.com
        </li>
        <li>
          <svg viewBox="0 0 24 24" aria-hidden="true"><circle cx="12" cy="12" r="10"/><path d="M2 12h20M12 2c3 3 3 17 0 20M12 2c-3 3-3 17 0 20" stroke="#1565bf" stroke-width="1.5" fill="none"/></svg>
          www.limbwellinc.com
        </li>
      </ul>
      <p class="address">1234, Address GoesHere, Country name , 12345</p>
    </div>
  </section>

</body>
</html>
```